Harborview Optical -Window Poster (Optometrist)

We are an optometry practice and we need a poster for a new store promotion for our window highlighting we now also sell 2 pairs of glasses as a package deal. The size will be 1300mm width x 1900mm height

The artwork will be displayed as a fabric banner in our shop window. We have 7 other banners with different services our business provides. The words needs to standout for passers by and the cars stopped at the traffic lights out front of our business. We already have signs with our logos phone number etc. so we won't need them included in the poster.

It would need to include the following information.

Two pair packages now available*

*Conditions apply

The artwork will be displayed as a fabric banner in our shop window. We have 7 other banners with different services our business provides. The words needs to standout for passers by and the cars stopped at the traffic lights out front of our business. We already have signs with our logos phone number etc. so we won't need them included in the poster. Thank you for your work it's amazing Added Saturday, February 18, 2017

The artwork will be displayed as a fabric banner in our shop window. We have 7 other banners with different services our business provides. The words needs to standout for passers by and the cars stopped at the traffic lights out front of our business. We already have signs with our logos phone number etc. so we won't need them included in the poster. Added Saturday, February 18, 2017

Target Market(s)

Cars driving past and stopped at traffic lights outside our store.

Industry/Entity Type

Optician

Requirements
Must have
• Poster must say:
• Two pair packages now available*
• *Conditions apply

```html
<!DOCTYPE html>
<html lang="en">
<head>
<meta charset="utf-8">
<title>Harborview Optical – Two Pair Packages Window Poster</title>
<link rel="stylesheet" href="https://fonts.googleapis.com/css2?family=Archivo+Black&family=Libre+Baskerville:wght@700&family=Oswald:wght@500&display=swap">
<style>
  :root {
    --poster-bg: #1a1a25;
    --band: #0d0b1e;
    --white: #ffffff;
    --yellow: #f5ec00;
    --retina-light: #ef5a45;
    --retina-mid: #d9442f;
    --retina-dark: #a92a22;
    --equipment: #2a2a36;
  }
  html, body {
    margin: 0;
    padding: 0;
    width: 962px;
    height: 1200px;
    overflow: hidden;
    background: var(--poster-bg);
  }
  .poster {
    position: relative;
    width: 962px;
    height: 1200px;
    background: var(--poster-bg);
    overflow: hidden;
  }
  .poster__equipment-photo {
    position: absolute;
    left: 0;
    top: 780px;
    width: 962px;
    height: 420px;
    background: radial-gradient(ellipse at 50% 45%, var(--equipment) 0%, var(--poster-bg) 70%);
  }
  .poster__retina-photo {
    position: absolute;
    left: 0;
    top: 0;
    width: 962px;
    height: 1200px;
  }
  .band {
    position: absolute;
    left: 23px;
    width: 920px;
    background: var(--band);
    display: flex;
    align-items: center;
    justify-content: center;
  }
  .band--top { top: 227px; height: 194px; }
  .band--bottom { top: 600px; height: 193px; }
  .headline {
    margin: 0;
    font-family: "Archivo Black", "Arial Black", sans-serif;
    line-height: 1;
    white-space: nowrap;
  }
  .headline--two-pair {
    color: var(--white);
    font-size: 132px;
    letter-spacing: 2px;
    transform: scaleX(1.05);
    margin-top: 10px;
  }
  .headline--packages {
    color: var(--yellow);
    font-size: 100px;
    letter-spacing: 3px;
    transform: scaleX(1.12);
    margin-left: 44px;
    margin-top: 10px;
  }
  .availability {
    position: absolute;
    left: 0;
    width: 962px;
    top: 884px;
    margin: 0;
    text-align: center;
    font-family: "Libre Baskerville", "Times New Roman", serif;
    font-weight: 700;
    font-size: 52px;
    color: var(--white);
    letter-spacing: 2px;
    line-height: 1;
  }
  .availability__mark {
    font-size: 58px;
    vertical-align: 22px;
    margin-left: 2px;
  }
  .conditions {
    position: absolute;
    left: 122px;
    top: 1020px;
    width: 745px;
    height: 73px;
    border: 3px solid var(--white);
    display: flex;
    align-items: center;
    justify-content: center;
    font-family: "Oswald", "Arial Narrow", sans-serif;
    font-weight: 500;
    font-size: 48px;
    letter-spacing: 3px;
    color: var(--white);
    margin: 0;
  }
</style>
</head>
<body>
  <main class="poster">
    <div class="poster__equipment-photo" role="img" aria-label="Faint dark photograph of an optometrist's eye-testing phoropter"></div>

    <svg class="poster__retina-photo" width="962" height="1200" viewBox="0 0 962 1200" role="img" aria-label="Close-up photograph of a red retina with blood vessels">
      <defs>
        <radialGradient id="retina-tone" cx="55%" cy="48%" r="60%">
          <stop offset="0%" stop-color="var(--retina-light)"/>
          <stop offset="65%" stop-color="var(--retina-mid)"/>
          <stop offset="100%" stop-color="var(--retina-dark)"/>
        </radialGradient>
      </defs>
      <ellipse cx="466" cy="482" rx="422" ry="351" fill="url(#retina-tone)"/>
    </svg>

    <div class="band band--top">
      <h1 class="headline headline--two-pair">TWO PAIR</h1>
    </div>
    <div class="band band--bottom">
      <h2 class="headline headline--packages">PACKAGES</h2>
    </div>

    <p class="availability">NOW AVAILABLE<span class="availability__mark">*</span></p>

    <p class="conditions">*CONDITIONS APPLY</p>
  </main>
</body>
</html>
```